Flat Belly Design Graphics for Social

I want to create 9 social media graphics (new Instagram size 4:5 (1080 x 1350 pixels) focusing on our Flat Belly Graphics, using the pics attached. Use the attached pics, NO RANDOM STOCK PHOTOGRAPHY. For the color scheme of the graphics, the color palette is attached. YOU MUST POST ALL 9 GRAPHICS IN ONE ENTRY.
Using the 3 titles below, create one set of graphics. 1) with all text, then for the others, use the pictures as detailed below in IMPORTANT:
1. Ten-Week Bright Morning Reboot
2. The Quick Garden Kitchen Menu Guide
3. Studio Habits for Lasting Energy Past Midlife - Zero Gym Needed
IMPORTANT:
Only use RK Pic 1 and RK Pic 2 with the title, Ten-Week Bright Morning Reboot
Only use meal plan1 and meal plan2 pics with the title, Quick Garden Kitchen Menu Guide
Only use studio habits 1 and studio habits 2 pics with the title, Studio Habits for Lasting Energy Past Midlife - Zero Gym Needed
women over 40

```html
<!DOCTYPE html>
<html lang="en">
<head>
<meta charset="utf-8">
<title>Social Graphics Set</title>
<link href="https://fonts.googleapis.com/css2?family=Poppins:wght@600;700;800&family=Oswald:wght@600;700&family=Playfair+Display:ital,wght@0,600;1,500;1,600&family=Great+Vibes&family=Michroma&family=Cinzel:wght@600&display=swap" rel="stylesheet">
<style>
:root{
  --stage:#252525;
  --blush:#fbeaec;
  --blush-soft:#f7d8de;
  --rose:#e39aae;
  --rose-deep:#cf5a8f;
  --teal:#247a68;
  --teal-dark:#1e5246;
  --slate:#2d4a45;
  --white:#ffffff;
}
*{margin:0;padding:0;box-sizing:border-box}
html,body{width:960px;height:1200px;overflow:hidden;background:var(--stage)}
.canvas{position:relative;width:960px;height:1200px;background:var(--stage)}
.card{position:absolute;width:231px;height:288px;overflow:hidden;background:var(--blush)}
.col-a{left:110px}.col-b{left:363px}.col-c{left:616px}
.row-a{top:132px}.row-b{top:452px}.row-c{top:772px}
.t{position:absolute;white-space:nowrap;line-height:1}
.poppins{font-family:'Poppins',sans-serif;font-weight:800}
.oswald{font-family:'Oswald',sans-serif;font-weight:700}
.playfair{font-family:'Playfair Display',serif}
.photo{position:absolute}
.center{left:0;right:0;text-align:center}

/* card 1 */
.c1-top{left:14px;top:18px;font-size:31px;color:var(--rose)}
.c1-main{left:8px;top:62px;font-size:48px;color:var(--teal);letter-spacing:-1px}
.c1-sub{left:9px;top:120px;font-size:34px;color:var(--slate)}
.c1-rule{position:absolute;height:1px;background:var(--rose-deep)}
.c1-band{position:absolute;left:0;right:0;top:234px;height:28px;background:var(--rose-deep)}
.c1-band-text{top:238px;font-family:'Playfair Display',serif;font-style:italic;font-weight:500;font-size:21px;color:var(--white)}

/* card 2 */
.c2-col{position:absolute;inset:0}
.c2-left{left:8px;font-size:40px;color:var(--blush);font-weight:600;letter-spacing:-.5px}
.c2-right{left:122px;font-size:30px;font-weight:600}

/* card 3 */
.c3-head{position:absolute;left:0;right:0;top:0;height:114px;background:var(--rose)}
.c3-script{font-family:'Great Vibes',cursive;font-size:28px;color:var(--teal-dark);top:116px}
.c3-line{position:absolute;left:16px;right:16px;top:237px;height:3px;background:var(--rose)}

/* card 5 / 8 ribbons */
.ribbon{position:absolute;background:var(--rose)}
</style>
</head>
<body>
<main class="canvas">

  <!-- Text-only: Ten-Week Bright Morning Reboot -->
  <section class="card col-a row-a">
    <p class="t poppins c1-top">TEN-WEEK</p>
    <p class="t poppins c1-main">BRIGHT</p>
    <p class="t poppins c1-sub">MORNING</p>
    <span class="c1-rule" style="left:125px;right:0;top:230px"></span>
    <div class="c1-band"></div>
    <p class="t center c1-band-text">REBOOT</p>
    <span class="c1-rule" style="left:0;width:105px;top:265px"></span>
  </section>

  <!-- Text-only: Quick Garden Kitchen Menu Guide -->
  <section class="card col-b row-a">
    <svg class="c2-col" width="231" height="288" viewBox="0 0 231 288" aria-hidden="true">
      <polygon points="0,0 98,0 98,110 114,144 98,178 98,288 0,288" fill="#e39aae"/>
      <polygon points="98,0 104,0 104,110 120,144 104,178 104,288 98,288 98,178 114,144 98,110" fill="#f4c6d2"/>
    </svg>
    <p class="t oswald c2-left" style="top:86px">THE</p>
    <p class="t oswald c2-left" style="top:140px;font-size:34px">QUICK</p>
    <p class="t oswald c2-right" style="top:38px;color:var(--teal-dark)">GARDEN</p>
    <p class="t oswald c2-right" style="top:96px;color:var(--slate)">KITCHEN</p>
    <p class="t oswald c2-right" style="top:154px;color:var(--rose-deep)">MENU</p>
    <p class="t oswald c2-right" style="top:212px;color:var(--rose-deep)">GUIDE</p>
  </section>

  <!-- Text-only: Studio Habits -->
  <section class="card col-c row-a">
    <div class="c3-head"></div>
    <p class="t poppins center" style="top:14px;font-size:37px;color:var(--blush)">STUDIO</p>
    <p class="t poppins center" style="top:56px;font-size:40px;color:var(--blush)">HABITS</p>
    <p class="t center c3-script">for</p>
    <p class="t poppins center" style="top:158px;font-size:22px;color:var(--teal-dark)">LASTING ENERGY</p>
    <p class="t poppins center" style="top:196px;font-size:26px;color:var(--rose)">PAST MIDLIFE</p>
    <span class="c3-line"></span>
    <p class="t center" style="top:252px;font-family:'Poppins',sans-serif;font-weight:700;font-size:14px;color:var(--teal-dark)">ZERO GYM NEEDED</p>
  </section>

  <!-- Photo: Ten-Week Bright Morning Reboot -->
  <section class="card col-a row-b">
    <svg class="photo" style="left:0;top:0" width="231" height="288" aria-hidden="true">
      <circle cx="172" cy="158" r="60" fill="#f7d8de"/>
    </svg>
    <div class="photo" role="img" aria-label="Smiling woman in a cropped white sweater pointing at her waist" style="left:95px;top:98px;width:136px;height:190px;background:linear-gradient(180deg,#efe6e4 0%,#d9c7c2 55%,#2b2628 100%);border-radius:60px 60px 0 0"></div>
    <p class="t" style="left:8px;top:22px;font-family:'Michroma',sans-serif;font-size:20px;color:var(--teal)">TEN-WEEK</p>
    <p class="t poppins" style="left:10px;top:60px;font-size:44px;font-weight:700;color:var(--slate)">BRIGHT</p>
    <p class="t poppins" style="left:10px;top:120px;font-size:31px;font-weight:700;color:var(--slate)">MORNING</p>
    <p class="t poppins" style="left:13px;top:172px;font-size:24px;font-weight:700;color:var(--rose-deep)">RE-</p>
    <p class="t poppins" style="left:13px;top:206px;font-size:24px;font-weight:700;color:var(--rose-deep)">BOOT</p>
  </section>

  <!-- Photo: Quick Garden Kitchen Menu Guide -->
  <section class="card col-b row-b">
    <div class="photo" role="img" aria-label="Overhead spread of chicken, fruit, vegetables and grains around a menu sheet on a wooden table" style="left:0;top:0;width:231px;height:147px;background:radial-gradient(circle at 50% 55%,#eeeeee 0 18%,transparent 19%),linear-gradient(135deg,#d9b9a5 0%,#7c5a45 45%,#b3574f 70%,#8b6a3e 100%)"></div>
    <p class="t center playfair" style="top:160px;font-style:italic;font-weight:600;font-size:22px;color:var(--teal)">The Quick</p>
    <p class="t center poppins" style="top:187px;font-weight:700;font-size:22px;color:var(--slate)">GARDEN KITCHEN</p>
    <svg class="photo" style="left:8px;top:220px" width="215" height="38" aria-hidden="true">
      <polygon points="0,6 6,0 6,32 0,38" fill="#e39aae"/>
      <polygon points="215,6 209,0 209,32 215,38" fill="#e39aae"/>
      <rect x="5" y="3" width="205" height="32" fill="#e39aae"/>
    </svg>
    <p class="t center poppins" style="top:226px;font-weight:600;font-size:25px;color:var(--white)">MENU GUIDE</p>
  </section>

  <!-- Photo: Studio Habits -->
  <section class="card col-c row-b">
    <div class="photo" role="img" aria-label="Two women sharing a surprised whisper, tinted in rose" style="inset:0;background:linear-gradient(160deg,#c98a98 0%,#d98f9e 40%,#e6a0ad 75%,#d3899c 100%)"></div>
    <div class="photo" style="left:12px;top:20px;width:208px;height:32px;background:var(--teal-dark)"></div>
    <p class="t oswald center" style="top:22px;font-size:25px;color:var(--white);letter-spacing:-.3px">STUDIO HABITS</p>
    <p class="t center" style="top:57px;font-family:'Poppins',sans-serif;font-weight:600;font-size:18px;color:var(--white)">FOR LASTING ENERGY</p>
    <p class="t poppins center" style="top:82px;font-weight:700;font-size:33px;color:var(--white)">PAST MIDLIFE</p>
    <p class="t oswald center" style="top:182px;font-size:36px;color:var(--white)">ZERO GYM</p>
    <p class="t oswald center" style="top:224px;font-size:36px;color:var(--white)">NEEDED</p>
  </section>

  <!-- Photo: Ten-Week Bright Morning Reboot, kitchen -->
  <section class="card col-a row-c">
    <div class="photo" role="img" aria-label="Smiling woman in a cropped white sweater standing in a warm wooden kitchen" style="inset:0;background:linear-gradient(180deg,#c9a98f 0%,#8a5d45 45%,#e9e1dd 62%,#6d4634 100%)"></div>
    <svg class="photo" style="left:0;top:0" width="231" height="288" aria-hidden="true">
      <circle cx="108" cy="48" r="124" fill="#f4c6d2" opacity=".55"/>
      <circle cx="102" cy="42" r="118" fill="#fce9ee"/>
    </svg>
    <p class="t poppins center" style="top:8px;font-weight:700;font-size:24px;color:var(--teal-dark)">TEN-WEEK</p>
    <p class="t poppins center" style="top:40px;font-weight:700;font-size:23px;color:var(--teal-dark)">BRIGHT MORNING</p>
    <p class="t oswald center" style="top:238px;font-size:36px;color:var(--white);letter-spacing:-.5px">REBOOT</p>
  </section>

  <!-- Photo: Quick Garden Kitchen Menu Guide, diamond -->
  <section class="card col-b row-c">
    <div class="photo" role="img" aria-label="Fresh salmon, eggs, avocado, fruit and vegetables arranged on a dark table" style="left:0;top:130px;width:231px;height:158px;background:linear-gradient(135deg,#5d8a3a 0%,#c04a37 30%,#3d2e26 55%,#d65b3b 80%,#6f9a3f 100%)"></div>
    <svg class="photo" style="left:0;top:0" width="231" height="288" aria-hidden="true">
      <polygon points="0,0 231,0 231,130 0,130" fill="#f8e6ea"/>
      <polygon points="115,0 231,108 231,124 115,10 0,124 0,108" fill="#f4c6d2"/>
      <polygon points="115,18 231,126 115,248 0,126" fill="#e39aae"/>
    </svg>
    <p class="t center" style="top:60px;font-family:'Cinzel',serif;font-weight:600;font-size:19px;color:var(--white)">THE</p>
    <p class="t center" style="top:86px;font-family:'Cinzel',serif;font-weight:600;font-size:19px;color:var(--white)">QUICK</p>
    <p class="t poppins center" style="top:114px;font-weight:600;font-size:20px;color:#fbeaec">GARDEN KITCHEN</p>
    <p class="t playfair center" style="top:148px;font-weight:600;font-size:26px;color:var(--teal-dark)">MENU</p>
    <p class="t playfair center" style="top:175px;font-weight:600;font-size:26px;color:var(--teal-dark)">GUIDE</p>
  </section>

  <!-- Photo: Studio Habits, whisper -->
  <section class="card col-c row-c">
    <div class="photo" style="inset:0;background:var(--rose)"></div>
    <div class="photo" role="img" aria-label="Two women, one whispering a secret to the other who looks amazed" style="left:95px;top:0;width:136px;height:193px;background:linear-gradient(160deg,#d7a595 0%,#e8c2b2 45%,#c99580 70%,#8fb3cf 100%)"></div>
    <p class="t oswald" style="left:12px;top:20px;font-size:18px;font-weight:600;color:var(--blush)">STUDIO</p>
    <p class="t oswald" style="left:12px;top:50px;font-size:18px;font-weight:600;color:var(--blush)">HABITS</p>
    <p class="t oswald" style="left:12px;top:80px;font-size:18px;font-weight:600;color:var(--blush)">FOR</p>
    <p class="t oswald" style="left:12px;top:106px;font-size:26px;color:var(--white)">LASTING</p>
    <p class="t oswald" style="left:12px;top:143px;font-size:26px;color:var(--white)">ENERGY</p>
    <div class="photo" style="left:0;top:193px;width:231px;height:60px;background:var(--blush-soft)"></div>
    <p class="t oswald center" style="top:200px;font-size:38px;color:var(--teal-dark);letter-spacing:-.5px">PAST MIDLIFE</p>
    <p class="t center" style="top:263px;font-family:'Poppins',sans-serif;font-weight:600;font-size:13px;color:var(--teal-dark)">ZERO GYM NEEDED</p>
  </section>

</main>
</body>
</html>
```